Veldmark Supplies Business Card

Professional business card that stand out to our potential customers. Front and back with clean modern design

Industry/Entity Type

Oil and gas

Contact Information for Business Card

Name, address, website , office phone and cell number

Requirements
Must have
• Editable files for each employee

```html
<!DOCTYPE html>
<html lang="en">
<head>
<meta charset="utf-8">
<title>Veldmark Supplies Business Card</title>
<link rel="stylesheet" href="https://fonts.googleapis.com/css2?family=Poppins:wght@300;400;700;800&display=swap">
<style>
  :root {
    --stage: #2b2624;
    --card: #1b1b1c;
    --red: #ff0d0d;
    --cyan: #05aed3;
    --ink: #f2f2f2;
  }
  * { margin: 0; padding: 0; box-sizing: border-box; }
  html, body { width: 1200px; height: 842px; overflow: hidden; }
  body {
    background: var(--stage);
    font-family: "Poppins", sans-serif;
    display: flex;
    align-items: center;
    justify-content: center;
    gap: 40px;
  }
  .card {
    position: relative;
    width: 540px;
    height: 309px;
    background: var(--card);
    overflow: hidden;
    box-shadow: 0 10px 30px rgba(0,0,0,0.45);
  }

  /* Contact side */
  .band-top { position: absolute; top: 0; left: 0; right: 0; height: 14px; background: var(--red); }
  .band-bottom { position: absolute; bottom: 0; left: 0; right: 0; height: 16px; background: var(--cyan); }
  .contact {
    position: absolute;
    inset: 14px 0 16px;
    display: flex;
    flex-direction: column;
    align-items: center;
    justify-content: center;
    color: var(--ink);
    text-align: center;
    padding-bottom: 20px;
  }
  .person-name {
    font-weight: 800;
    font-size: 22px;
    letter-spacing: 0.5px;
    line-height: 1;
  }
  .person-name .first { color: var(--red); }
  .person-name .last { color: var(--cyan); }
  .rule { width: 62px; height: 2px; margin: 14px 0 10px; }
  .rule.red { background: var(--red); }
  .rule.cyan { background: var(--cyan); margin: 10px 0 12px; }
  .contact-lines { font-size: 15px; font-weight: 400; line-height: 1.35; }
  .address { font-size: 13px; font-weight: 300; line-height: 1.4; letter-spacing: 0.3px; }

  /* Brand side */
  .edge-mark { position: absolute; height: 92px; display: flex; gap: 5px; }
  .edge-mark .bar { width: 30px; background: var(--cyan); }
  .edge-mark .line { width: 4px; background: var(--red); }
  .edge-mark.left { left: 0; top: 150px; }
  .edge-mark.right { right: 0; top: 60px; flex-direction: row-reverse; }
  .brand {
    position: absolute;
    left: 0; right: 0;
    top: 196px;
    display: flex;
    align-items: center;
    justify-content: center;
    gap: 14px;
  }
  .brand-square { width: 22px; height: 22px; background: var(--red); }
  .brand-name {
    font-weight: 800;
    font-size: 30px;
    letter-spacing: 1px;
    color: var(--red);
    text-transform: uppercase;
    line-height: 1;
  }
</style>
</head>
<body>

  <section class="card card-contact">
    <div class="band-top"></div>
    <div class="contact">
      <h1 class="person-name"><span class="first">MARTEN</span> <span class="last">KOLBY</span></h1>
      <div class="rule red"></div>
      <p class="contact-lines">+1 432 555 0184<br>+1 432 555 0172<br>www.veldmarksupplies.com</p>
      <div class="rule cyan"></div>
      <p class="address">1180 BASIN RIDGE ROAD, SUITE 4<br>88210, HOLLEN COUNTY</p>
    </div>
    <div class="band-bottom"></div>
  </section>

  <section class="card card-brand">
    <div class="edge-mark left"><div class="bar"></div><div class="line"></div></div>
    <div class="edge-mark right"><div class="bar"></div><div class="line"></div></div>
    <div class="brand">
      <div class="brand-square"></div>
      <h2 class="brand-name">Veldmark Supplies</h2>
    </div>
  </section>

</body>
</html>
```